New Business Card Design Project

Use the flyer uploaded and website www.brightoakbuilders.com for inspiration.
List Our Services on Backside of business cards
Marcus Delling
Harborline Builders Inc.
Licensed General Contractors
858-471-6093

Contact Information for Business Card

Use the flyer uploaded and website www.brightoakbuilders.com for inspiration. List Our Services on Backside of business cards Marcus Delling Harborline Builders Inc. Licensed General Contractors 858-471-6093

```html
<!DOCTYPE html>
<html lang="en">
<head>
<meta charset="utf-8">
<title>Harborline Builders – Business Card</title>
<link href="https://fonts.googleapis.com/css2?family=Montserrat:wght@400;500;700&display=swap" rel="stylesheet">
<style>
  :root {
    --page-bg: #2a2a2c;
    --card-bg: #141414;
    --ink: #f4f4f4;
    --ink-soft: #d8d8d8;
    --rule: #bdbdbd;
  }
  * { margin: 0; padding: 0; box-sizing: border-box; }
  html, body {
    width: 1200px; height: 900px; overflow: hidden;
    background: var(--page-bg);
    font-family: 'Montserrat', sans-serif;
    color: var(--ink);
  }
  .canvas {
    width: 1200px; height: 900px;
    display: flex; flex-direction: column;
    align-items: center; justify-content: center; gap: 30px;
  }
  .card {
    width: 700px; height: 400px;
    background: var(--card-bg);
    border-radius: 22px;
    position: relative;
    box-shadow: 0 18px 40px rgba(0,0,0,.45);
  }
  /* Back side */
  .card--back { display: flex; align-items: center; }
  .back__brand {
    width: 50%; display: flex; justify-content: center; align-items: center;
  }
  .brand-name {
    font-weight: 400; text-transform: uppercase;
    letter-spacing: 0.16em; color: var(--ink);
  }
  .back__brand .brand-name { font-size: 22px; text-align: center; line-height: 1.4; }
  .back__divider {
    width: 1px; height: 190px; background: var(--rule);
  }
  .services { padding-left: 34px; }
  .services__title { font-size: 19px; font-weight: 700; margin-bottom: 8px; }
  .services__list { list-style: none; font-size: 14.5px; line-height: 1.62; color: var(--ink-soft); }
  .services__list li::before { content: "•"; margin-right: 9px; color: var(--ink); }
  /* Front side */
  .front__info {
    position: absolute; left: 330px; top: 54px; right: 40px;
  }
  .front__info .brand-name { font-size: 22px; margin-bottom: 44px; }
  .person__name { font-size: 26px; font-weight: 700; }
  .person__title { font-size: 15px; color: var(--ink-soft); margin-top: 2px; }
  .address { font-size: 14.5px; line-height: 1.45; color: var(--ink-soft); margin-top: 24px; }
  .contacts { list-style: none; margin-top: 20px; font-size: 14.5px; line-height: 2; }
  .contacts li { display: flex; align-items: center; gap: 12px; }
  .contacts svg { width: 13px; height: 13px; fill: var(--ink); flex: none; }
</style>
</head>
<body>
<main class="canvas">
  <section class="card card--back">
    <div class="back__brand">
      <p class="brand-name">Harborline<br>Builders</p>
    </div>
    <div class="back__divider"></div>
    <div class="services">
      <h2 class="services__title">Our Services</h2>
      <ul class="services__list">
        <li>Remodel: Kitchen &amp; Bath</li>
        <li>Painting: Interior &amp; Exterior</li>
        <li>Flooring: Carpet, Vinyl, Wood</li>
        <li>Window &amp; Door Replacement</li>
        <li>Plumbing: Repair &amp; Upgrades</li>
        <li>Energy Efficienct Upgrades</li>
        <li>Deck &amp; Patio construction</li>
        <li>Water &amp; Mold Damage</li>
        <li>Garage Renovation</li>
      </ul>
    </div>
  </section>

  <section class="card card--front">
    <div class="front__info">
      <p class="brand-name">Harborline Builders</p>
      <h1 class="person__name">Marcus Delling</h1>
      <p class="person__title">Licensed General Contractors</p>
      <p class="address">48 Lantern Way, suite 210<br>Ridgefield PA 18440</p>
      <ul class="contacts">
        <li><svg viewBox="0 0 16 16" aria-hidden="true"><path d="M3 1h3l1.5 4-2 1.3a9 9 0 0 0 4.2 4.2L11 8.5l4 1.5v3a2 2 0 0 1-2 2A12 12 0 0 1 1 3a2 2 0 0 1 2-2z"/></svg>858-471-6093</li>
        <li><svg viewBox="0 0 16 16" aria-hidden="true"><path d="M1 3h14v10H1z M1 3l7 6 7-6" fill="none" stroke="#f4f4f4" stroke-width="1.6"/></svg>info@brightoakbuilders.com</li>
        <li><svg viewBox="0 0 16 16" aria-hidden="true"><circle cx="8" cy="8" r="6.5" fill="none" stroke="#f4f4f4" stroke-width="1.5"/><path d="M1.5 8h13M8 1.5c-3 3.5-3 9.5 0 13M8 1.5c3 3.5 3 9.5 0 13" fill="none" stroke="#f4f4f4" stroke-width="1.2"/></svg>www.brightoakbuilders.com</li>
      </ul>
    </div>
  </section>
</main>
</body>
</html>
```